Business Card Design (NEW FILES)

ATTENTION: New vector files are available. Please update your design to reflect/use the new (better resolution) logo images.

Seeking a unique and professional business card design for a commercial drone photography/videography business. The layout should feature
the logo (attached) and include the following information:
Owen Tarrick
614-502-7738
www.skylarkreelworks.example
NRD Certified Remote Pilot

Owen Tarrick

```html
<!DOCTYPE html>
<html lang="en">
<head>
<meta charset="utf-8">
<title>Skylark Reelworks – Business Card</title>
<link href="https://fonts.googleapis.com/css2?family=Open+Sans:wght@400;600;700&display=swap" rel="stylesheet">
<style>
  :root {
    --stage: #232323;
    --navy: #1b1f55;
    --navy-deep: #161a4a;
    --navy-raised: #262c70;
    --orange: #ec8a4f;
    --paper: #ffffff;
    --ink: #1b1f55;
  }
  * { box-sizing: border-box; margin: 0; padding: 0; }
  html, body { width: 1200px; height: 780px; overflow: hidden; }
  body {
    background: var(--stage);
    font-family: "Open Sans", Arial, sans-serif;
    position: relative;
  }
  .card {
    position: absolute;
    top: 236px;
    width: 540px;
    height: 308px;
    overflow: hidden;
    box-shadow: 0 14px 30px rgba(0,0,0,.45);
  }
  .card--front { left: 45px; background: var(--paper); }
  .card--back  { left: 615px; background: var(--navy-deep); }

  .brand {
    position: absolute;
    display: flex;
    align-items: center;
    gap: 10px;
  }
  .brand__dot {
    width: 22px; height: 22px; border-radius: 50%;
    background: var(--orange);
  }
  .brand__name {
    font-weight: 600;
    letter-spacing: .5px;
  }
  .card--front .brand { left: 30px; top: 30px; }
  .card--front .brand__name { font-size: 26px; color: var(--ink); }

  .contact {
    position: absolute;
    left: 30px; top: 96px;
    color: var(--ink);
    font-size: 13px;
    line-height: 20px;
    list-style: none;
  }
  .contact__item { display: flex; align-items: center; gap: 7px; }
  .contact__item--plain { padding-left: 0; }
  .contact__icon { width: 11px; height: 11px; flex: none; }

  .swoosh { position: absolute; left: 0; bottom: 0; width: 540px; height: 308px; }

  .person {
    position: absolute;
    right: 60px; top: 186px;
    text-align: right;
  }
  .person__name { font-size: 28px; font-weight: 700; line-height: 1; }
  .person__first { color: var(--orange); }
  .person__last { color: var(--ink); }
  .person__role { font-size: 14px; color: var(--ink); margin-top: 6px; letter-spacing: .5px; }

  .corner-tab {
    position: absolute;
    right: 0; top: 236px;
    width: 40px; height: 40px;
    background: var(--orange);
  }

  .card--back .brand {
    left: 50%; top: 50%;
    transform: translate(-50%, -50%);
  }
  .card--back .brand__name { font-size: 34px; color: var(--navy-raised); }
</style>
</head>
<body>
  <section class="card card--front" aria-label="Business card, front">
    <div class="brand">
      <span class="brand__dot"></span>
      <span class="brand__name">Skylark Reelworks</span>
    </div>

    <ul class="contact">
      <li class="contact__item">NRD Certified Remote Pilot</li>
      <li class="contact__item">Fully Insured</li>
      <li class="contact__item">
        <svg class="contact__icon" viewBox="0 0 12 12" aria-hidden="true"><path d="M2.5 1h2l1 3-1.3 1a7 7 0 0 0 2.8 2.8l1-1.3 3 1v2a1 1 0 0 1-1 1A10 10 0 0 1 1.5 2a1 1 0 0 1 1-1z" fill="#ec8a4f"/></svg>
        614-502-7738
      </li>
      <li class="contact__item">
        <svg class="contact__icon" viewBox="0 0 12 12" aria-hidden="true"><circle cx="6" cy="6" r="5" fill="none" stroke="#ec8a4f" stroke-width="1.4"/><path d="M1 6h10M6 1c-2.5 3-2.5 7 0 10M6 1c2.5 3 2.5 7 0 10" fill="none" stroke="#ec8a4f" stroke-width="1"/></svg>
        www.skylarkreelworks.example
      </li>
    </ul>

    <svg class="swoosh" viewBox="0 0 540 308" aria-hidden="true">
      <path d="M0 0 L0 308 L300 308 C230 290 120 220 0 0 Z" fill="#1b1f55" transform="translate(0,0)" opacity="0"/>
      <path d="M0 308 L0 258 C110 262 190 282 300 308 Z" fill="#1b1f55"/>
      <path d="M0 0 L0 0" />
      <path d="M0 232 C110 240 200 262 300 308 L282 308 C190 270 100 252 0 246 Z" fill="#ec8a4f"/>
    </svg>

    <div class="person">
      <p class="person__name"><span class="person__first">Owen</span> <span class="person__last">Tarrick</span></p>
      <p class="person__role">Owner</p>
    </div>
    <div class="corner-tab"></div>
  </section>

  <section class="card card--back" aria-label="Business card, back">
    <div class="brand">
      <span class="brand__dot"></span>
      <span class="brand__name">Skylark Reelworks</span>
    </div>
  </section>
</body>
</html>
```